Professional Single Page Website Design for Tollbrook Advisory

Tollbrook Advisory is a new business consultancy specializing in providing expert services to small businesses, primarily in the brick-and-mortar retail and food service sectors. We offer a range of services including franchise development and launch, due diligence, and construction management.

Currently, we have a basic website set up at www.tollbrookadvisory.example, but we need a professional touch to enhance its design and functionality.

Project Requirements:
- Single Page Design: For now, we need a single page design that effectively showcases who we are, our services, and contact information.
- Future Expansion: The design should be flexible and scalable for future expansion to include additional pages like specific service offerings, about us, and a dedicated contact page.
- Design Aesthetic: We are looking for a modern yet professional design that aligns with our brand identity.
- Logo: We have a logo that we like, which was also sourced from Pixel Bazaar. The logo files are attached to this project brief.

Key Sections to Include:
- Hero Section: An engaging introduction to Tollbrook Advisory with a strong visual impact.
- About Us: A brief overview of who we are and our mission.
- Team: Section for the profiles of the two principals.
- Services: A clear and concise presentation of our services, including franchise development, due diligence, and construction management.
- Contact Information: Easy-to-find contact details, including a form for inquiries.
- Call to Action: Encouraging visitors to get in touch with us for consultations or further information.

Design Considerations:
- Ensure the design is responsive and mobile-friendly.
- Include high-quality images and icons that complement our services and industry.
- We do not need development services, this is only a design project.

```html
<!DOCTYPE html>
<html lang="en">
<head>
<meta charset="utf-8">
<title>Tollbrook Advisory</title>
<link rel="stylesheet" href="https://fonts.googleapis.com/css2?family=Poppins:ital,wght@0,400;0,500;0,600;0,700;0,800;1,400&family=Roboto:ital,wght@0,400;0,500;0,700;1,400;1,500;1,700&display=swap">
<style>
:root{
  --green:#5f9e87;
  --green-light:#84bda3;
  --navy:#27303c;
  --navy-2:#2c3644;
  --ink:#1f2329;
  --text:#3a3f45;
  --white:#ffffff;
  --black:#050505;
  --line:#6f86a8;
}
*{box-sizing:border-box;margin:0;padding:0}
html,body{width:1200px;height:3701px;overflow:hidden;background:var(--white)}
body{font-family:"Roboto",sans-serif;color:var(--text)}
.page{position:relative;width:1200px;height:3701px;overflow:hidden}
.abs{position:absolute}
.btn{position:absolute;display:flex;align-items:center;justify-content:center;color:var(--white);font-family:"Roboto",sans-serif;font-weight:500;font-size:15px;letter-spacing:.3px;text-transform:uppercase}
.btn::before{content:"";position:absolute;inset:0;background:var(--green);transform:skewX(-12deg);z-index:-1}
.btn span{position:relative}

/* header */
.brand{position:absolute;display:flex;align-items:center;gap:12px;font-family:"Poppins",sans-serif;font-weight:600}
.brand .dot{width:44px;height:44px;border-radius:50%;background:var(--green)}
.header-brand{left:112px;top:30px;color:var(--green);font-size:24px;line-height:1.05}
.nav{position:absolute;left:408px;top:42px;display:flex;gap:0;font-size:16px;color:var(--ink)}
.nav a{text-decoration:none;color:inherit;margin-right:42px}
.nav a.active{color:var(--green);font-weight:500}
.hero-photo{position:absolute;left:513px;top:0}
.diamond{position:absolute;width:14px;height:14px;border:2px solid var(--green-light);transform:rotate(45deg);border-radius:2px}

.hero-title{position:absolute;left:108px;top:150px;font-family:"Poppins",sans-serif;font-weight:600;font-size:70px;line-height:1;color:var(--navy)}
.hero-title .accent{display:block;color:var(--green);font-weight:500;font-size:56px;margin-top:8px}
.hero-tag{position:absolute;left:110px;top:293px;font-size:20px;color:var(--ink)}
.hero-lead{position:absolute;left:112px;top:342px;font-size:20px;font-style:italic;color:var(--ink)}
.hero-lead b{font-weight:700}
.hero-copy{position:absolute;left:112px;top:374px;width:530px;font-size:15px;line-height:28.4px;color:var(--ink)}

/* services */
.services{position:absolute;left:0;top:681px;width:1200px;height:741px}
.service-tabs{position:absolute;left:0;top:0;width:234px;height:741px}
.service-tab{position:absolute;left:0;width:234px;height:146px;background:var(--navy-2);color:var(--white);font-weight:700;font-size:16.5px;line-height:26px;display:flex;align-items:center;justify-content:center;text-align:center;padding:0 14px}
.service-tab.active{background:var(--green)}
.service-tab.active::after{content:"";position:absolute;right:-20px;top:50%;margin-top:-12px;border-left:20px solid var(--green);border-top:12px solid transparent;border-bottom:12px solid transparent}
.service-photo{position:absolute;left:235px;top:0;width:965px;height:741px;background:linear-gradient(90deg,#4a4c50 0%,#6d6f72 35%,#b5b2ae 70%,#d6d2cc 100%)}
.service-title{position:absolute;left:292px;top:127px;font-family:"Poppins",sans-serif;font-weight:800;font-size:36px;color:var(--white)}
.service-sub{position:absolute;left:297px;top:203px;font-family:"Poppins",sans-serif;font-weight:500;font-size:22px;line-height:30px;color:var(--white)}
.service-copy{position:absolute;left:302px;top:282px;width:434px;font-size:15px;line-height:25.7px;text-align:justify;color:#eceae6}

/* about */
.about-mark{position:absolute;left:112px;top:1556px;width:442px;height:442px;display:flex;align-items:center;justify-content:center;gap:18px;font-family:"Poppins",sans-serif;font-weight:700;font-size:40px;color:var(--ink)}
.about-mark .sq{width:60px;height:60px;background:var(--ink);border-radius:10px;flex:none}
.about-title{position:absolute;left:601px;top:1508px;font-family:"Poppins",sans-serif;font-weight:800;font-size:34px;color:var(--ink)}
.about-copy{position:absolute;left:601px;top:1575px;width:488px;font-size:15px;line-height:26.5px;text-align:justify;color:var(--ink)}
.mission{position:absolute;left:601px;top:1823px;display:flex;align-items:center;gap:10px;font-family:"Poppins",sans-serif;font-weight:600;font-size:19px;color:var(--ink)}
.mission-copy{position:absolute;left:600px;top:1872px;width:476px;font-size:15px;line-height:26.5px;text-align:justify;color:var(--ink)}

/* team */
.team{position:absolute;left:0;top:2132px;width:1200px;height:597px;background:linear-gradient(100deg,#4f7e74 0%,#679f8b 45%,#86c0a5 100%)}
.team-title{position:absolute;left:0;top:52px;width:1200px;text-align:center;font-family:"Poppins",sans-serif;font-weight:800;font-size:36px;color:var(--white)}
.member-name{position:absolute;left:112px;top:183px;font-family:"Poppins",sans-serif;font-weight:800;font-size:32px;color:var(--white)}
.member-role{position:absolute;left:112px;top:230px;font-family:"Poppins",sans-serif;font-weight:700;font-size:17px;color:var(--white)}
.member-links{position:absolute;left:112px;top:263px;display:flex;gap:20px;font-weight:700;font-size:16px;color:var(--white)}
.member-links span{display:flex;align-items:center;gap:6px}
.member-bio{position:absolute;left:112px;top:308px;width:270px;font-size:15px;line-height:25.7px;color:#f2f6f4}
.arrow-btn{position:absolute;top:474px;width:30px;height:30px;border-radius:50%;border:2px solid var(--white);display:flex;align-items:center;justify-content:center}
.arrow-btn.filled{background:var(--white)}
.member-card{position:absolute;top:151px;width:333px;height:390px;border-radius:10px;overflow:hidden}
.member-card .photo{position:absolute;inset:0 0 60px 0}
.member-card .label{position:absolute;left:0;right:0;bottom:0;height:60px;background:var(--navy-2);color:var(--white);font-family:"Poppins",sans-serif;font-weight:800;font-size:20px;display:flex;align-items:center;justify-content:center}

/* contact */
.contact-card{position:absolute;left:108px;top:2834px;width:977px;height:414px;background:var(--white);border-radius:16px;box-shadow:0 4px 24px rgba(0,0,0,.08);z-index:2}
.contact-panel{position:absolute;left:21px;top:16px;width:388px;height:379px;background:var(--navy);border-radius:14px;color:var(--white)}
.contact-panel h2{position:absolute;left:76px;top:30px;font-family:"Poppins",sans-serif;font-weight:700;font-size:34px}
.c-item{position:absolute;left:78px;display:flex;gap:16px;align-items:flex-start}
.c-ico{width:42px;height:42px;border-radius:50%;background:#d9e3f3;display:flex;align-items:center;justify-content:center;flex:none;margin-top:6px}
.c-item strong{display:block;font-family:"Poppins",sans-serif;font-weight:600;font-size:20px;line-height:26px}
.c-item p{font-size:15px;line-height:24px}
.field{position:absolute;width:231px;border-bottom:1.5px solid var(--line);font-size:14px;color:#6c7280;padding-bottom:6px}
.submit{position:absolute;left:625px;top:310px;width:136px;height:46px;font-size:16px}

/* footer */
.footer-shape{position:absolute;left:0;top:3170px;z-index:1}
.footer{position:absolute;left:0;top:3170px;width:1200px;height:531px;z-index:3;color:var(--white)}
.footer-brand{left:112px;top:176px;font-size:26px;line-height:1.05;color:var(--white)}
.footer-brand .dot{background:var(--white);width:52px;height:52px}
.f-head{position:absolute;font-family:"Poppins",sans-serif;font-weight:700;font-size:20px}
.f-links{position:absolute;left:402px;top:198px;list-style:none;font-size:15px}
.f-links li{height:43px}
.f-item{position:absolute;left:593px;display:flex;gap:14px}
.f-item .c-ico{width:44px;height:44px;margin-top:4px}
.f-item strong{display:block;font-family:"Poppins",sans-serif;font-weight:500;font-size:20px;line-height:24px}
.f-item p{font-size:15px;line-height:24px}
.socials{position:absolute;left:912px;top:190px;display:flex;gap:8px}
.socials span{width:34px;height:34px;border-radius:50%;background:var(--white)}
.copyright{position:absolute;left:0;top:487px;width:1200px;text-align:center;font-size:15px;padding-right:0}
</style>
</head>
<body>
<div class="page">

  <!-- header & hero -->
  <svg class="hero-photo" width="687" height="582" viewBox="0 0 687 582" role="img" aria-label="Photo of two business professionals reviewing a tablet in a bright office">
    <defs>
      <linearGradient id="heroGrad" x1="0" y1="0" x2="1" y2="1">
        <stop offset="0" stop-color="#e9ecee"/>
        <stop offset=".45" stop-color="#8a9da3"/>
        <stop offset="1" stop-color="#3a4450"/>
      </linearGradient>
    </defs>
    <path d="M90 0 H687 V300 L440 560 Q400 600 360 560 L40 220 Q0 170 30 110 Z" fill="url(#heroGrad)"/>
  </svg>

  <div class="brand header-brand"><span class="dot"></span><span>Tollbrook<br>Advisory</span></div>
  <nav class="nav">
    <a class="active">Home</a><a>About Us</a><a>Team</a><a>Services</a><a>Contact Us</a>
  </nav>
  <div class="btn" style="left:952px;top:32px;width:134px;height:46px"><span>Get a Quote</span></div>

  <span class="diamond" style="left:512px;top:222px"></span>
  <span class="diamond" style="left:516px;top:308px"></span>
  <span class="diamond" style="left:712px;top:451px"></span>
  <span class="diamond" style="left:509px;top:531px"></span>

  <h1 class="hero-title">Tollbrook<span class="accent">Advisory</span></h1>
  <p class="hero-tag">Building Success in Southern California</p>
  <p class="hero-lead"><b>Expertise At Every Step:</b> From Planning to Execution</p>
  <p class="hero-copy" style="top:370px">At Tollbrook, we blend innovative strategies with local market expertise to guide your commercial real estate ventures. Whether you're launching a new restaurant, investing in retail spaces, or expanding a franchise, our dedicated team is here to turn your real estate aspirations into tangible success. Dive into a partnership that grows with you.</p>
  <div class="btn" style="left:114px;top:523px;width:136px;height:46px"><span>Get Started</span></div>

  <!-- services -->
  <section class="services">
    <div class="service-photo" role="img" aria-label="Photo of colleagues shaking hands across a meeting table in an office"></div>
    <div class="service-tabs">
      <div class="service-tab" style="top:0">Franchise Development &amp; Launch</div>
      <div class="service-tab" style="top:149px">Due Diligence</div>
      <div class="service-tab active" style="top:298px">Building &amp; Construction Management</div>
      <div class="service-tab" style="top:447px">Investment Property Evaluation</div>
      <div class="service-tab" style="top:596px;height:145px">Market Analysis &amp; Feasibility Studies</div>
    </div>
    <h2 class="service-title">Tollbrook Services</h2>
    <h3 class="service-sub">Building &amp; Construction<br>Management</h3>
    <div class="service-copy">
      <p>Our Building &amp; Construction Management Services oversee every aspect of your construction and development projects, from initial planning to final completion. We ensure projects stay on time and within budget, providing meticulous attention to detail and proactive problem-solving.</p>
      <p style="margin-top:25px">Specializing in tenant improvements (TIs) and ground-up construction for small to mid-size commercial projects, we handle everything from permitting and contractor coordination to quality control and final inspections. Trust us to deliver successful projects that meet your specifications and exceed your expectations, ensuring a smooth and efficient construction process every step of the way.</p>
    </div>
  </section>

  <!-- about -->
  <div class="about-mark"><span class="sq"></span><span>Tollbrook<br>Advisory</span></div>
  <h2 class="about-title">About Us</h2>
  <p class="about-copy">Welcome to Tollbrook Advisory, your trusted partner in navigating the complexities of the real estate and small business markets. Founded by industry veterans Victor Almeda and Dean Harlow, we specialize in providing comprehensive services tailored to the unique needs of our clients. Whether you're a franchisee, a new restaurant owner, or a commercial real estate investor, our expertise in due diligence, construction management, and investment property evaluation ensures you make informed, strategic decisions.</p>
  <div class="mission">
    <svg width="42" height="42" viewBox="0 0 42 42" aria-hidden="true">
      <circle cx="20" cy="22" r="17" fill="none" stroke="#1f2329" stroke-width="4"/>
      <circle cx="20" cy="22" r="9" fill="none" stroke="#1f2329" stroke-width="4"/>
      <circle cx="20" cy="22" r="3" fill="#1f2329"/>
      <path d="M20 22 L36 6 M31 4 L38 4 L38 11" fill="none" stroke="#1f2329" stroke-width="3"/>
    </svg>
    <span>MISSION</span>
  </div>
  <p class="mission-copy">Discover how Tollbrook Advisory can support your business journey. Partner with us and experience the difference our dedication and expertise can make.</p>
  <div class="btn" style="left:602px;top:1966px;width:136px;height:46px"><span>Learn More</span></div>

  <!-- team -->
  <section class="team">
    <h2 class="team-title">Our Leadership Team</h2>
    <h3 class="member-name">Dean Harlow</h3>
    <p class="member-role">Principal</p>
    <div class="member-links">
      <span><svg width="20" height="15" viewBox="0 0 20 15"><rect width="20" height="15" rx="2" fill="#fff"/><path d="M1 2 L10 9 L19 2" fill="none" stroke="#5f9e87" stroke-width="2"/></svg>Email:</span>
      <span><svg width="16" height="16" viewBox="0 0 24 24"><path d="M6.6 10.8c1.4 2.8 3.8 5.1 6.6 6.6l2.2-2.2c.3-.3.7-.4 1-.2 1.1.4 2.3.6 3.6.6.6 0 1 .4 1 1V20c0 .6-.4 1-1 1C10.6 21 3 13.4 3 4c0-.6.4-1 1-1h3.5c.6 0 1 .4 1 1 0 1.3.2 2.5.6 3.6.1.3 0 .7-.2 1z" fill="#fff"/></svg>Phone</span>
    </div>
    <p class="member-bio">Dean Harlow is a seasoned real estate expert with extensive experience in project and construction management, and a licensed real estate agent in California. Fluent in both English and Korean,...</p>
    <div class="arrow-btn filled" style="left:112px"><svg width="12" height="12" viewBox="0 0 12 12"><path d="M8 1 L3 6 L8 11" fill="none" stroke="#5f9e87" stroke-width="2"/></svg></div>
    <div class="arrow-btn" style="left:156px"><svg width="12" height="12" viewBox="0 0 12 12"><path d="M4 1 L9 6 L4 11" fill="none" stroke="#fff" stroke-width="2"/></svg></div>
    <div class="member-card" style="left:407px">
      <div class="photo" role="img" aria-label="Portrait photo of Dean Harlow" style="background:linear-gradient(180deg,#e6e6e4,#b9b1a8 70%,#3b3f48)"></div>
      <div class="label">Dean Harlow</div>
    </div>
    <div class="member-card" style="left:757px">
      <div class="photo" role="img" aria-label="Portrait photo of Victor Almeda outdoors" style="background:linear-gradient(180deg,#a9b8c4,#d7d6d2 45%,#f1efea)"></div>
      <div class="label">Victor Almeda</div>
    </div>
  </section>

  <!-- contact -->
  <section class="contact-card">
    <div class="contact-panel">
      <h2>Contact Us</h2>
      <div class="c-item" style="top:100px">
        <span class="c-ico"><svg width="20" height="15" viewBox="0 0 20 15"><rect width="20" height="15" rx="2" fill="#27303c"/><path d="M1 2 L10 9 L19 2" fill="none" stroke="#d9e3f3" stroke-width="2"/></svg></span>
        <div><strong>Email:</strong><p>info@tollbrookadvisory.example</p></div>
      </div>
      <div class="c-item" style="top:178px">
        <span class="c-ico"><svg width="20" height="20" viewBox="0 0 24 24"><path d="M6.6 10.8c1.4 2.8 3.8 5.1 6.6 6.6l2.2-2.2c.3-.3.7-.4 1-.2 1.1.4 2.3.6 3.6.6.6 0 1 .4 1 1V20c0 .6-.4 1-1 1C10.6 21 3 13.4 3 4c0-.6.4-1 1-1h3.5c.6 0 1 .4 1 1 0 1.3.2 2.5.6 3.6.1.3 0 .7-.2 1z" fill="#27303c"/></svg></span>
        <div><strong>Phone No:</strong><p>+1(555) 010 0199</p></div>
      </div>
      <div class="c-item" style="top:257px">
        <span class="c-ico"><svg width="18" height="22" viewBox="0 0 18 22"><path d="M9 0C4 0 0 4 0 9c0 6 9 13 9 13s9-7 9-13c0-5-4-9-9-9z" fill="#27303c"/><circle cx="9" cy="9" r="3.5" fill="#d9e3f3"/></svg></span>
        <div><strong>Location:</strong><p>418 Harbor Crest Ave Suite 200<br>418 Harbor Crest Ave, Costa Vista,<br>CA 90210</p></div>
      </div>
    </div>
    <div class="field" style="left:448px;top:68px">Your Name</div>
    <div class="field" style="left:714px;top:68px">Last Name</div>
    <div class="field" style="left:448px;top:159px">Email Address</div>
    <div class="field" style="left:714px;top:159px">Phone</div>
    <div class="field" style="left:448px;top:253px">Company</div>
    <div class="field" style="left:714px;top:253px">Additional Information</div>
    <div class="btn submit"><span>Submit</span></div>
  </section>

  <!-- footer -->
  <svg class="footer-shape" width="1200" height="531" viewBox="0 0 1200 531" aria-hidden="true">
    <path d="M0 160 C250 100 500 80 700 78 L1085 78 L1085 0 Q1160 20 1200 75 L1200 531 L0 531 Z" fill="#050505"/>
  </svg>
  <footer class="footer">
    <div class="brand footer-brand"><span class="dot"></span><span>Tollbrook<br>Advisory</span></div>
    <h4 class="f-head" style="left:402px;top:150px">Quick Links</h4>
    <ul class="f-links">
      <li>Home</li><li>About Us</li><li>Team</li><li>Services</li><li>Contact Us</li>
    </ul>
    <h4 class="f-head" style="left:591px;top:150px">Contact Us</h4>
    <div class="f-item" style="top:196px">
      <span class="c-ico"><svg width="20" height="15" viewBox="0 0 20 15"><rect width="20" height="15" rx="2" fill="#27303c"/><path d="M1 2 L10 9 L19 2" fill="none" stroke="#d9e3f3" stroke-width="2"/></svg></span>
      <div><strong>Email:</strong><p>info@tollbrookadvisory.example</p></div>
    </div>
    <div class="f-item" style="top:275px">
      <span class="c-ico"><svg width="20" height="20" viewBox="0 0 24 24"><path d="M6.6 10.8c1.4 2.8 3.8 5.1 6.6 6.6l2.2-2.2c.3-.3.7-.4 1-.2 1.1.4 2.3.6 3.6.6.6 0 1 .4 1 1V20c0 .6-.4 1-1 1C10.6 21 3 13.4 3 4c0-.6.4-1 1-1h3.5c.6 0 1 .4 1 1 0 1.3.2 2.5.6 3.6.1.3 0 .7-.2 1z" fill="#27303c"/></svg></span>
      <div><strong>Phone No:</strong><p>+1(555) 010 0199</p></div>
    </div>
    <div class="f-item" style="top:354px">
      <span class="c-ico"><svg width="18" height="22" viewBox="0 0 18 22"><path d="M9 0C4 0 0 4 0 9c0 6 9 13 9 13s9-7 9-13c0-5-4-9-9-9z" fill="#27303c"/><circle cx="9" cy="9" r="3.5" fill="#d9e3f3"/></svg></span>
      <div><strong>Location:</strong><p>418 Harbor Crest Ave Suite 200<br>418 Harbor Crest Ave, Costa Vista,<br>CA 90210</p></div>
    </div>
    <h4 class="f-head" style="left:908px;top:148px">Follow Us</h4>
    <div class="socials"><span></span><span></span><span></span></div>
    <p class="copyright">Copyright © 2024 Tollbrook Advisory | All Rights Reserved</p>
  </footer>

</div>
</body>
</html>
```